Local Flower Farm Needs Business Card Design

I need business cards designed for a flower farm based in Eudora, Kansas.
Business Info:
We are a local cut flower farm located in Eudora, Kansas, founded by Corinne Haldwick. What started as a passion for agriculture and search for more joy in daily life has blossomed into a small business dedicated to providing the community with beautiful, fresh, and sustainable flowers. We specialize in local, seasonal blooms, ensuring that every petal reflects the care and dedication we pour into our craft. Our mission is to deliver the highest quality flowers directly to our customers through local farmers markets and to florists who share our commitment to sustainability. Join us in celebrating the beauty of nature, one bloom at a time!
Contact Details:
Corinne Haldwick
Owner
Phone 913-555-0147
Facebook: Rosalind Thorpe Gardens
Instagram: @RosalindThorpeGardens
Website: RosalindThorpeGardens.example
Target Market(s)
Wholesale to Florists and Direct to Consumer via Farmers Market
Industry/Entity Type
Florist, Farm
Contact Information for Business Card
Name, Contact Info, Logo
Look and feel
Each slider illustrates characteristics of the customer's brand and the style your logo design should communicate.

```html
<!DOCTYPE html>
<html lang="en">
<head>
<meta charset="utf-8">
<title>Rosalind Thorpe Gardens – Business Card</title>
<link rel="stylesheet" href="https://fonts.googleapis.com/css2?family=Roboto:wght@400;500;700&display=swap">
<style>
  :root {
    --bg: #e9ebea;
    --forest: #0f2d32;
    --forest-deep: #0b2428;
    --teal: #1e6266;
    --paper: #ffffff;
    --ink-light: #f2f5f4;
    --ink-muted: #b9c6c5;
  }
  * { box-sizing: border-box; margin: 0; padding: 0; }
  html, body { width: 1200px; height: 900px; overflow: hidden; }
  body {
    background: var(--bg);
    font-family: "Roboto", Arial, sans-serif;
    position: relative;
  }
  .card {
    position: absolute;
    left: 320px;
    width: 560px;
    height: 320px;
    border-radius: 22px;
    overflow: hidden;
    box-shadow: 0 10px 28px rgba(0,0,0,.18);
  }
  .card--front { top: 100px; background: var(--paper); }
  .card--back {
    top: 480px;
    background: linear-gradient(160deg, var(--forest) 0%, var(--forest-deep) 100%);
    display: flex; align-items: center; justify-content: center;
  }
  .card__shape { position: absolute; inset: 0; width: 100%; height: 100%; }
  .contact {
    position: absolute;
    left: 30px;
    top: 44px;
    width: 226px;
    color: var(--ink-light);
  }
  .contact__name { font-size: 22px; font-weight: 700; letter-spacing: .2px; white-space: nowrap; }
  .contact__role { font-size: 12px; color: var(--ink-muted); margin-top: 2px; }
  .contact__rule { width: 14px; height: 1px; background: var(--ink-muted); margin: 8px 0 16px; }
  .contact__list { list-style: none; }
  .contact__item {
    display: flex; align-items: center; gap: 8px;
    font-size: 14px; line-height: 1; margin-bottom: 10px;
    white-space: nowrap;
  }
  .contact__icon { width: 12px; height: 12px; flex: none; }
  .brand {
    position: absolute;
    display: flex; align-items: center; justify-content: center;
    width: 170px; height: 170px;
    border-radius: 50%;
    text-align: center;
    font-family: "Roboto", Arial, sans-serif;
    font-weight: 500;
    font-size: 17px;
    line-height: 1.3;
    letter-spacing: 1.5px;
    text-transform: uppercase;
  }
  .card--front .brand {
    left: 355px; top: 75px;
    border: 1.5px solid var(--forest);
    color: var(--forest);
  }
  .card--back .brand {
    position: static;
    border: 1.5px solid var(--ink-light);
    color: var(--ink-light);
  }
</style>
</head>
<body>

  <section class="card card--front" aria-label="Business card front">
    <svg class="card__shape" viewBox="0 0 560 320" preserveAspectRatio="none" aria-hidden="true">
      <rect width="560" height="320" fill="var(--paper)"/>
      <path d="M0 0 H330 C276 80 258 190 280 320 H0 Z" fill="var(--forest)"/>
      <path d="M330 0 H344 C290 80 272 190 294 320 H280 C258 190 276 80 330 0 Z" fill="var(--teal)"/>
      <path d="M346 0 C292 80 274 190 296 320" fill="none" stroke="var(--paper)" stroke-width="3"/>
    </svg>

    <div class="contact">
      <h1 class="contact__name">Corinne Haldwick</h1>
      <p class="contact__role">Owner</p>
      <div class="contact__rule"></div>
      <ul class="contact__list">
        <li class="contact__item">
          <svg class="contact__icon" viewBox="0 0 12 12" aria-hidden="true"><path d="M2.5 1 L4.5 1 L5.3 3.6 L4 4.6 C4.7 6 6 7.3 7.4 8 L8.4 6.7 L11 7.5 L11 9.5 C11 10.3 10.3 11 9.5 11 C5 11 1 7 1 2.5 C1 1.7 1.7 1 2.5 1 Z" fill="currentColor"/></svg>
          (913)555-0147
        </li>
        <li class="contact__item">
          <svg class="contact__icon" viewBox="0 0 12 12" aria-hidden="true"><circle cx="6" cy="6" r="5.5" fill="currentColor"/></svg>
          Rosalind Thorpe Gardens
        </li>
        <li class="contact__item">
          <svg class="contact__icon" viewBox="0 0 12 12" aria-hidden="true"><circle cx="6" cy="6" r="5" fill="none" stroke="currentColor" stroke-width="1.3"/></svg>
          @RosalindThorpeGardens
        </li>
        <li class="contact__item">
          <svg class="contact__icon" viewBox="0 0 12 12" aria-hidden="true"><circle cx="6" cy="6" r="5" fill="none" stroke="currentColor" stroke-width="1.3"/><path d="M1 6 H11 M6 1 C3.5 3.5 3.5 8.5 6 11 M6 1 C8.5 3.5 8.5 8.5 6 11" fill="none" stroke="currentColor" stroke-width="1"/></svg>
          RosalindThorpeGardens.example
        </li>
      </ul>
    </div>

    <div class="brand">Rosalind<br>Thorpe<br>Gardens</div>
  </section>

  <section class="card card--back" aria-label="Business card back">
    <div class="brand">Rosalind<br>Thorpe<br>Gardens</div>
  </section>

</body>
</html>
```